Classy, Elegant, Simple Business Card Design

Looking to have a classy, simple, and elegant design. Want a top notch designed business card. I really like the look of the new torvane credit card. I also like the design I attached. I am trying to reach 21-29 year old females for booking us for there wedding or event. We offer Disc Jockey Service, Photo Booth Rentals, and Uplighting .

Target Market(s)

21-28 year old females

Contact Information for Business Card

Has to have logo, website, email, and phone number

Font styles to use
Other font styles liked:
• open to font choice, modern, clean
Designer to choose
33a6d7
0791cd
0555a3
ffffff

Requirements
Must have
• Has to have logo, website, email, and phone number
Nice to have
• I really like the design of the new torvane credit card. I also included my logo and some designs I like
Should not have
• clutter or too much info

```html
<!DOCTYPE html>
<html lang="en">
<head>
<meta charset="UTF-8">
<title>Tidelight Event Group – Business Card</title>
<link rel="stylesheet" href="https://fonts.googleapis.com/css2?family=Jost:wght@400;500&display=swap">
<style>
  :root {
    --backdrop: #e9e9e7;
    --card: #ffffff;
    --silver: #a8a8a8;
    --silver-dark: #9a9a9a;
    --card-shadow: rgba(0, 0, 0, 0.12);
  }
  * { margin: 0; padding: 0; box-sizing: border-box; }
  html, body {
    width: 1200px;
    height: 900px;
    overflow: hidden;
    background: var(--backdrop);
    font-family: "Jost", "Helvetica Neue", Arial, sans-serif;
  }
  .canvas {
    position: relative;
    width: 1200px;
    height: 900px;
  }
  .card {
    position: absolute;
    width: 520px;
    height: 300px;
    background: var(--card);
    border-radius: 18px;
    box-shadow: 0 6px 18px var(--card-shadow);
    color: var(--silver);
  }
  /* Brand side */
  .card--brand {
    left: 340px;
    top: 110px;
  }
  .brand-lockup {
    position: absolute;
    left: 0;
    right: 0;
    top: 112px;
    display: flex;
    align-items: center;
    justify-content: center;
    gap: 12px;
  }
  .brand-dot {
    width: 14px;
    height: 14px;
    border-radius: 50%;
    background: var(--silver);
  }
  .brand-name {
    font-weight: 500;
    font-size: 30px;
    letter-spacing: 2px;
    text-transform: uppercase;
    color: var(--silver);
  }
  .brand-web {
    position: absolute;
    right: 40px;
    bottom: 34px;
    font-size: 15px;
    letter-spacing: 1px;
    color: var(--silver);
  }
  /* Contact side */
  .card--contact {
    left: 340px;
    top: 490px;
  }
  .contact-brand {
    position: absolute;
    left: 44px;
    top: 42px;
    display: flex;
    align-items: center;
    gap: 10px;
  }
  .contact-brand .brand-name {
    font-size: 24px;
  }
  .contact-brand .brand-dot {
    width: 11px;
    height: 11px;
  }
  .contact-details {
    position: absolute;
    left: 44px;
    top: 160px;
  }
  .person-name {
    font-weight: 500;
    font-size: 21px;
    letter-spacing: 1px;
    color: var(--silver-dark);
    margin-bottom: 14px;
    padding-left: 12px;
  }
  .contact-line {
    font-size: 16px;
    letter-spacing: 0.6px;
    line-height: 1.6;
  }
  .contact-label {
    font-weight: 500;
    margin-right: 6px;
  }
</style>
</head>
<body>
<main class="canvas">
  <section class="card card--brand" aria-label="Business card front">
    <div class="brand-lockup">
      <span class="brand-dot"></span>
      <span class="brand-name">Tidelight Event Group</span>
    </div>
    <p class="brand-web">www.tidelighteventgroup.com</p>
  </section>

  <section class="card card--contact" aria-label="Business card back">
    <div class="contact-brand">
      <span class="brand-dot"></span>
      <span class="brand-name">Tidelight</span>
    </div>
    <div class="contact-details">
      <p class="person-name">Daniel M. Harper</p>
      <p class="contact-line"><span class="contact-label">P :</span>555 013 2468</p>
      <p class="contact-line"><span class="contact-label">E :</span>info@tidelighteventgroup.com</p>
    </div>
  </section>
</main>
</body>
</html>
```